Irrigation Business needs their business cards modernised and revamped

I would like to keep my current logo, colours and revamp the format of the card.

I would like the card to be clean yet important.

Im not sure if you include texture but i would like the named logo to be indented into the card etc.

show me something alive and free something thats clinical to the point yet has a feel of achievement. i would like people to go nice card.

Target Market(s)

high end clients, corporate, sports field manger, the guys that make the decisions

Industry/Entity Type

Business

Contact Information for Business Card

nformation to be included

Dean Harlow (Director)
0487305526
dean@kolvat.biz
www.kestonfieldworks.com

instagram logo
google logo
facebook logo

Colors

Designer to choose colors to be used in the design.

Requirements
Nice to have
• indentations a really nice feel to the card good texture

```html
<!DOCTYPE html>
<html lang="en">
<head>
<meta charset="utf-8">
<title>Keston Fieldworks – Business Card</title>
<link href="https://fonts.googleapis.com/css2?family=Montserrat:wght@700&family=Oswald:wght@500&family=Roboto:wght@400;500&display=swap" rel="stylesheet">
<style>
  :root {
    --stage: #e9ebee;
    --brand-blue: #3b70b4;
    --brand-blue-deep: #2c5fa8;
    --brand-cyan: #2aa3d0;
    --accent-green: #3cb56a;
    --card-white: #fbfbfb;
    --ink-grey: #4a4a4a;
    --rule-light: rgba(255,255,255,0.45);
  }
  * { margin: 0; padding: 0; box-sizing: border-box; }
  html, body {
    width: 1200px; height: 886px; overflow: hidden;
    background: var(--stage);
  }
  .stage { position: relative; width: 1200px; height: 886px; }

  .card {
    position: absolute;
    border-radius: 22px;
    box-shadow: 0 10px 28px rgba(0,0,0,0.18);
    overflow: hidden;
  }

  /* Front: blue side */
  .card-front {
    left: 160px; top: 293px; width: 520px; height: 300px;
    background: var(--brand-blue);
    color: #fff;
    text-align: center;
  }
  .brand-mark {
    width: 84px; height: 84px; border-radius: 50%;
    border: 4px solid #fff;
    margin: 58px auto 18px;
  }
  .brand-name {
    font-family: "Montserrat", sans-serif;
    font-weight: 700;
    font-size: 30px;
    letter-spacing: 0.5px;
    color: #fff;
  }
  .social-row {
    position: absolute; left: 40px; right: 40px; bottom: 46px;
    display: flex; align-items: center; gap: 8px;
  }
  .social-row .rule { flex: 1; height: 1px; background: var(--rule-light); }
  .social-dot {
    width: 24px; height: 24px; border-radius: 50%;
    background: #fff;
  }

  /* Back: white side, portrait */
  .card-back {
    left: 740px; top: 183px; width: 300px; height: 520px;
    background: var(--card-white);
  }
  .contact {
    position: absolute; left: 0; right: 0; top: 56px;
    text-align: center;
  }
  .person-name {
    font-family: "Oswald", sans-serif;
    font-weight: 500;
    font-size: 30px;
    color: var(--brand-blue-deep);
    text-transform: uppercase;
    letter-spacing: 0.5px;
    line-height: 1.1;
  }
  .person-role {
    font-family: "Roboto", sans-serif;
    font-weight: 500;
    font-size: 14px;
    color: var(--accent-green);
    text-transform: uppercase;
    letter-spacing: 1px;
    margin-top: 4px;
  }
  .divider {
    width: 20px; height: 2px; background: var(--brand-blue-deep);
    margin: 14px auto 14px;
  }
  .contact-lines {
    list-style: none;
    font-family: "Roboto", sans-serif;
    font-weight: 400;
    font-size: 14px;
    line-height: 1.45;
    color: var(--ink-grey);
  }
  .emblem {
    position: absolute; left: 28px; bottom: 22px;
    width: 244px; height: 244px;
  }
</style>
</head>
<body>
<main class="stage">

  <section class="card card-front" aria-label="Card front">
    <div class="brand-mark"></div>
    <h1 class="brand-name">KESTON FIELDWORKS</h1>
    <div class="social-row">
      <span class="rule"></span>
      <span class="social-dot"></span>
      <span class="social-dot"></span>
      <span class="social-dot"></span>
      <span class="rule"></span>
    </div>
  </section>

  <section class="card card-back" aria-label="Card back">
    <div class="contact">
      <h2 class="person-name">Dean Harlow</h2>
      <p class="person-role">Director</p>
      <div class="divider"></div>
      <ul class="contact-lines">
        <li>0487305526</li>
        <li>dean@kolvat.biz</li>
        <li>www.kestonfieldworks.com</li>
      </ul>
    </div>
    <svg class="emblem" viewBox="0 0 244 244" aria-hidden="true">
      <defs>
        <linearGradient id="emblem-fill" x1="0" y1="0" x2="1" y2="0">
          <stop offset="0" stop-color="#2aa3d0"/>
          <stop offset="1" stop-color="#2c5fa8"/>
        </linearGradient>
      </defs>
      <circle cx="122" cy="122" r="118" fill="url(#emblem-fill)"/>
    </svg>
  </section>

</main>
</body>
</html>
```